Mobile Vantage Laser Tag Party Rental

I am a newbie to e-commerce and website development. I need website designed for my Mobile Vantage Laser Tag party rental business. I have already developed my company Logo and therefore I am looking to maximize my branding. Therefore, I have put some concept Ideas into a powerpoint presentation to sort of help promote some creativity (since I am not creative). What I am looking for is a site that I can take and continue to develop as time passes. I need the site to be highly interactive (I do not want static site) would like plenty of movement and clickable interaction/ sound is a plus. With plenty of Pictures (some I will provide at later date). The site should be informative as well as a platform for customers to be able to schedule an event and also make the necessary payment right online (call to action). I would like for the site to have a picture/video gallery for media that i will collect at a later date after providing services for my customers. (Also, Picutures can be used/not used or manipulate however creative you can be)

Target Market(s)

Ages 8-40

Primarily Teens (Video Gamers) Paintball & Airsoft players

Extreme Sports Fans/Live Action Gamers

College Students/Youth Groups

Corporate Managers and Team Leaders

Industry/Entity Type

E-Commerce

Requirements
Must have
• My Logos (I'll provide)
• My Color Scheme (Black, Ultra Lime Green (nearly Flourescent), Metallic Grey/Aluminum or Silver
• My Tag Line " Let's Get In The Game ! "
• Email/Phone/Birthday/Age Request forms for collection purposes
• Must have ability to make online payment
• Ability for customers to leave comments/or reviews
• links to social media
Should not have
• Should not be static (No Sound or No movement)

```html
<!DOCTYPE html>
<html lang="en">
<head>
<meta charset="utf-8">
<title>Vantage Laser Tag – Mobile Laser Tag Parties</title>
<link href="https://fonts.googleapis.com/css2?family=Carlito:wght@400;700&family=Open+Sans:wght@600;700&display=swap" rel="stylesheet">
<style>
:root{
  --lime:#7ef227;
  --black:#000;
  --charcoal:#2b2b2b;
  --white:#fff;
  --ink:#1a1a1a;
}
*{margin:0;padding:0;box-sizing:border-box}
html,body{width:924px;height:1200px;overflow:hidden;background:var(--black)}
body{position:relative;font-family:"Carlito",sans-serif;color:var(--white)}
.abs{position:absolute}

/* header */
.site-header{left:0;top:0;width:924px;height:113px;background:var(--black)}
.brand-dot{left:126px;top:52px;width:14px;height:14px;border-radius:50%;background:var(--lime)}
.brand-sub{left:146px;top:51px;font-size:12px;font-weight:700;color:var(--lime)}
.brand-name{left:246px;top:44px;font-size:24px;font-weight:700;color:var(--lime);letter-spacing:.5px}
.phone{right:100px;top:46px;font-family:"Open Sans",sans-serif;font-weight:600;font-size:21px;color:var(--white)}

/* event type bar */
.event-bar{left:0;top:113px;width:924px;height:29px;background:var(--lime);display:flex;align-items:center;padding-left:100px;gap:19px}
.event-bar a{color:var(--ink);font-size:10.5px;text-decoration:none}

/* main nav */
.main-nav{left:0;top:142px;width:924px;height:39px;background:var(--charcoal);display:flex;align-items:center;padding-left:99px}
.main-nav a{color:var(--white);font-weight:700;font-size:11.5px;text-decoration:none;margin-right:31px}
.social{right:100px;top:153px;display:flex;gap:6px}
.social span{width:14px;height:14px;border-radius:50%;background:var(--lime)}

/* hero */
.hero{left:0;top:181px;width:924px;height:250px;background:var(--lime)}
.hero-photo{left:77px;top:194px;width:770px;height:221px;background:linear-gradient(90deg,#3a3a3a,#8d8f90 45%,#a2a4a5 60%,#4a4a4a)}
.hero-card{left:100px;top:257px;width:231px;height:88px;background:var(--lime)}
.hero-card h1{position:absolute;left:15px;top:12px;font-weight:400;font-size:21px;color:var(--white);white-space:nowrap}
.hero-btn{position:absolute;left:15px;top:48px;width:104px;height:26px;background:var(--charcoal);color:var(--white);font-weight:700;font-size:10px;display:flex;align-items:center;justify-content:center}
.hero-dots{left:109px;top:382px;display:flex;gap:4px}
.hero-dots span{width:8px;height:8px;border-radius:50%;background:var(--white)}
.hero-dots span:first-child{background:var(--lime)}

/* about */
.about{left:101px;top:468px;width:459px}
.about h2{font-size:12.5px;color:var(--lime);font-weight:700;margin-bottom:17px}
.about .q{font-size:10.6px;margin-bottom:6px}
.about .a{font-size:10.6px;line-height:18.4px;text-align:justify;margin-bottom:23px}
.about .a.tight{margin-bottom:16px}

/* galleries */
.gallery-title{top:910px;font-size:12.5px;font-weight:700;color:var(--lime)}
.gallery-photo{top:934px;width:231px;height:132px}
.photo{left:100px;background:linear-gradient(135deg,#5f7a4c,#b7b0a3 55%,#4e5e3c)}
.video{left:346px;background:linear-gradient(135deg,#7a8a60,#2f3f5a 55%,#44543a)}
.arrow-btn{width:26px;height:26px;border-radius:50%;background:var(--lime);top:986px}
.mini-arrow{top:914px;width:13px;height:13px;border-radius:50%}
.play{left:442px;top:987px;width:36px;height:24px;background:rgba(0,0,0,.55)}
.progress{left:358px;top:1052px;width:160px;height:5px;background:#555}
.progress i{display:block;width:45px;height:5px;background:var(--lime)}

/* sidebar */
.panel{left:593px;width:231px;background:var(--white);color:var(--ink)}
.panel-head{background:var(--lime);padding:0 14px;color:var(--ink);font-weight:700;font-size:12.5px}
.book .panel-head{height:44px;text-align:center;padding-top:9px}
.book .panel-head small{display:block;font-weight:400;font-size:8.5px;color:#3d7b12;margin-top:2px}
.checkout{position:absolute;left:56px;top:55px;width:120px;height:37px;border:1.5px solid #2a4f8f;border-radius:2px;display:flex;align-items:center;justify-content:center;gap:4px}
.checkout span{width:20px;height:12px;background:#c9c9c9}
.news{top:576px;height:164px;background:var(--lime);padding:17px 13px}
.news h3{font-size:12.5px;color:var(--ink);margin-bottom:10px}
.news p{font-size:9.8px;color:var(--ink);line-height:24px}
.discount{top:753px;height:60px}
.discount .panel-head{height:33px;line-height:33px}
.discount p{text-align:center;font-size:9.8px;line-height:27px}
.links{top:828px;height:146px}
.links .panel-head{height:34px;line-height:34px}
.links ul{list-style:none;padding:12px 16px;font-size:9.8px;line-height:24.3px}
.badge-a{left:593px;top:992px;width:66px;height:74px;background:var(--white);border:3px solid #bbb}
.badge-b{left:666px;top:992px;width:100px;height:74px;background:radial-gradient(circle,#7ef227,#1d5a08)}

/* footer */
.site-footer{left:0;top:1114px;width:924px;height:86px;background:var(--lime);color:var(--ink)}
.foot-nav{position:absolute;left:99px;top:25px;font-size:10.5px;font-weight:700;display:flex;gap:11px}
.copyright{position:absolute;left:99px;top:52px;font-size:10px}
.foot-social{position:absolute;right:100px;top:30px;display:flex;gap:10px}
.foot-social span{width:22px;height:22px;border-radius:50%;background:var(--ink)}
</style>
</head>
<body>

<header class="abs site-header">
  <div class="abs brand-dot"></div>
  <div class="abs brand-sub">Vantage Tag Ops</div>
  <div class="abs brand-name">Vantage Laser Tag</div>
  <div class="abs phone">Call Us :(555) 014 -2290</div>
</header>

<nav class="abs event-bar">
  <a>Biirthday Parties</a><a>School/College Parties</a><a>Corporate Events</a><a>Military Groups</a><a>Fundraisers</a><a>Chruch Groups</a><a>Summer Camps</a>
</nav>

<nav class="abs main-nav">
  <a>HOME</a><a>GALLERIES</a><a>EVENT&nbsp; PACKAGES</a><a>ARMOREY</a><a>F.A.Q</a><a>ABOUT US</a>
</nav>
<div class="abs social" aria-label="Social media links"><span></span><span></span><span></span><span></span></div>

<section class="abs hero"></section>
<div class="abs hero-photo" role="img" aria-label="Players holding laser tag blasters beside a metal game emblem"></div>
<div class="abs hero-card">
  <h1>Let’s Get In The Game</h1>
  <div class="hero-btn">Find Out More</div>
</div>
<div class="abs hero-dots"><span></span><span></span><span></span><span></span></div>

<section class="abs about">
  <h2>About Vantage Laser Tag</h2>
  <p class="q">Q: What is Vantage Laser Tag &nbsp;?</p>
  <p class="a">A:&nbsp; Lorem ipsum dolor sit amet, consectetur adipisicing elit, sed do eiusmod tempor incididunt ut labore et dolore magna aliqua. Ut enim ad minim veniam, quis nostrud exercitation ullamco laboris nisi ut aliquip ex ea commodo consequat. Duis aute irure dolor in reprehenderit in voluptate velit esse cillum dolore eu fugiat nulla pariatur. Excepteur sint occaecat cupidatat non proident, sunt in culpa qui officia deserunt mollit anim id est laborum.</p>
  <p class="q" style="margin-top:9px">Q.&nbsp; Is it dangerous? Do the Taggers use actual lasers ?</p>
  <p class="a tight">A:&nbsp; Lorem ipsum dolor sit amet, consectetur adipisicing elit, sed do eiusmod tempor incididunt ut labore et dolore magna aliqua. Ut enim ad minim veniam, quis nostrud exercitation ullamco laboris nisi ut aliquip ex ea commodo consequat. Duis aute irure dolor in reprehenderit in voluptate velit esse cillum dolore eu fugiat nulla pariatur. Excepteur sint occaecat cupidatat non proident, sunt in culpa qui officia deserunt mollit anim id est laborum.</p>
  <p class="q">Q. Are there any limitations to where I can have my Vantage party</p>
  <p class="a">A:&nbsp; Lorem ipsum dolor sit amet, consectetur adipisicing elit, sed do eiusmod tempor incididunt ut labore et dolore magna aliqua. Ut enim ad minim veniam, quis nostrud exercitation ullamco laboris nisi ut aliquip ex ea commodo consequat. Duis aute irure dolor in reprehenderit in voluptate velit esse cillum dolore eu fugiat nulla pariatur. Excepteur sint occaecat cupidatat non proident, sunt in culpa qui officia deserunt mollit anim id est laborum.</p>
</section>

<div class="abs gallery-title" style="left:99px">PHOTO GALLERY</div>
<div class="abs gallery-title" style="left:347px">VIDEO GALLERY</div>
<div class="abs mini-arrow" style="left:546px;background:var(--white)"></div>
<div class="abs mini-arrow" style="left:563px;background:#777"></div>
<div class="abs gallery-photo photo" role="img" aria-label="Young player with headset in a wooded field"></div>
<div class="abs arrow-btn" style="left:109px"><svg width="26" height="26"><path d="M15 7 9 13l6 6" stroke="#000" stroke-width="3" fill="none"/></svg></div>
<div class="abs arrow-btn" style="left:299px"><svg width="26" height="26"><path d="M11 7l6 6-6 6" stroke="#000" stroke-width="3" fill="none"/></svg></div>
<div class="abs gallery-photo video" role="img" aria-label="Video still of kids in laser tag gear outdoors"></div>
<div class="abs play"><svg width="36" height="24"><path d="M14 6v12l10-6z" fill="#fff"/></svg></div>
<div class="abs progress"><i></i></div>

<aside>
  <div class="abs panel book" style="top:458px;height:104px">
    <div class="panel-head">Book Online<small>Reserve Your Campaign Now!</small></div>
    <div class="checkout" aria-label="Online payment options"><span></span><span></span><span></span><span></span></div>
  </div>
  <div class="abs panel news">
    <h3>News &amp; Events</h3>
    <p>6/24 - Sed ut perspiciatis unde omnis iste</p>
    <p>6/24 - natus error sit voluptatem accusantium</p>
    <p>6/24 - doloremque laudantium, totam</p>
    <p>6/24 - rem aperiam, eaque ipsa quae ab</p>
    <p>6/24 - illo inventore veritatis et quasi architecto</p>
  </div>
  <div class="abs panel discount">
    <div class="panel-head">Everyone likes Discounts</div>
    <p>Click Here&nbsp; to find out more</p>
  </div>
  <div class="abs panel links">
    <div class="panel-head">Helpful Links</div>
    <ul>
      <li>&gt;&gt; Sed ut perspiciatis unde omnis iste</li>
      <li>&gt;&gt; natus error sit voluptatem accusantium</li>
      <li>&gt;&gt; doloremque laudantium, totam</li>
      <li>&gt;&gt; rem aperiam, eaque ipsa quae ab</li>
    </ul>
  </div>
  <div class="abs badge-a" role="img" aria-label="Content rating badge"></div>
  <div class="abs badge-b" role="img" aria-label="Company badge on green burst"></div>
</aside>

<footer class="abs site-footer">
  <nav class="foot-nav">
    <span>HOME</span><span>|</span><span>GALLERIES</span><span>|</span><span>EVENT&nbsp; PACKAGES</span><span>|</span><span>ARMOREY</span><span>|</span><span>F.A.Q</span><span>|</span><span>ABOUT US</span>
  </nav>
  <p class="copyright">Copyright ©2013 Company Name&nbsp; - All rights reserved</p>
  <div class="foot-social" aria-label="Social media links"><span></span><span></span></div>
</footer>

</body>
</html>
```